Need webdesign for service company that provides Car hiring service and transit service

We need a web design for a company that provides airport transit services and transport services including Limo, Corporate cars, Disability transit, Family transit service. We need is a simple and professional design.

Below is site which we like and also offer the same service http://www.ridelarkway.com.au/
Updates

Project Deadline Extended
Reason: Waiting for the Feedback from multiple stakeholders. Need the time to select and approve the design

Target Market(s)

Tourism, Travel

Industry/Entity Type

Airport

Number of Pages Required

3 page

Font styles to use
Decorative
Script

Requirements
Must have
• Simple and Professional, Site we like http://www.ridelarkway.com.au/ and also need to mobile friendly
Should not have
• Shouldn't have too many images

```html
<!DOCTYPE html>
<html lang="en">
<head>
<meta charset="utf-8">
<title>Velocab – Private &amp; Business Transport</title>
<link rel="stylesheet" href="https://fonts.googleapis.com/css2?family=Roboto+Condensed:wght@400;700&family=Open+Sans:wght@400;600&display=swap">
<style>
:root{
  --ink:#1a1a1a;
  --white:#ffffff;
  --grey-panel:rgba(112,106,106,.93);
  --blue:#2f6fb5;
  --sky:#5cb8dc;
  --orange:#f7861c;
  --green:#6bb42d;
  --footer:#1d1d1d;
  --footer-line:#333;
  --btn-blue:#1f5aa8;
  --muted:#444;
}
*{margin:0;padding:0;box-sizing:border-box}
html,body{width:807px;height:1200px;overflow:hidden;background:var(--white)}
body{position:relative;font-family:"Open Sans",Arial,sans-serif;color:var(--ink)}
h1,h2,h3,h4,h5{font-weight:400}

/* header */
.site-header{position:absolute;left:0;top:0;width:807px;height:70px;background:var(--white);border-bottom:1px solid #ddd;z-index:3}
.brand{position:absolute;left:66px;top:13px;display:flex;align-items:center;gap:8px}
.brand-mark{width:36px;height:36px;border:2px solid var(--ink)}
.brand-name{font-family:"Roboto Condensed",sans-serif;font-weight:700;font-size:24px;line-height:22px;letter-spacing:.5px}
.brand-tag{font-size:5.5px;letter-spacing:.3px;color:var(--muted);margin-top:2px}
.header-tools{position:absolute;right:66px;top:24px;display:flex;align-items:center;gap:9px}
.login{background:#000;color:#fff;font-family:"Roboto Condensed",sans-serif;font-size:11px;padding:3px 14px;border-radius:2px;margin-left:10px}

/* hero */
.hero{position:absolute;left:0;top:70px;width:807px;height:450px;
  background:linear-gradient(180deg,#c9d6e3 0%,#e3e8ee 30%,#b9b6b2 60%,#d8d6d3 80%,#ffffff 100%)}
.hero-title{position:absolute;left:0;right:0;top:54px;text-align:center;font-family:"Roboto Condensed",sans-serif;font-weight:700;font-size:27px;color:#222}
.hero-sub{position:absolute;left:0;right:0;top:89px;text-align:center;font-size:13px;color:#222}
.hero-btn{position:absolute;left:398px;top:119px;width:69px;height:22px;background:#6d6a68;color:#fff;font-family:"Roboto Condensed",sans-serif;font-size:10px;display:flex;align-items:center;justify-content:center;border-radius:2px}
.slide-arrow{position:absolute;top:157px;width:24px;height:24px;border-radius:50%;background:rgba(120,120,120,.7)}

/* tiles */
.tile{position:absolute;color:#fff;z-index:2}
.tile h3{font-family:"Roboto Condensed",sans-serif}
.tile p{font-size:7.2px;line-height:13.6px}
.quote-box{left:66px;top:369px;width:219px;height:277px;background:var(--grey-panel);padding:22px 12px}
.quote-box h3{font-size:17px;margin-left:1px}
.field{background:#fff;height:25px;display:flex;align-items:center;gap:9px;padding-left:11px;font-size:6.5px;color:#444}
.field.origin{margin-top:16px}
.field.dest{margin-top:13px}
.opt{font-family:"Roboto Condensed",sans-serif;font-size:9.5px;display:flex;align-items:center;gap:6px}
.submit{margin-top:14px;height:26px;background:#000;border-radius:2px;display:flex;align-items:center;justify-content:center;font-family:"Roboto Condensed",sans-serif;font-size:11px}
.note{font-size:6.8px;margin-top:13px}
.welcome{left:290px;top:369px;width:288px;height:122px;background:var(--blue);padding:22px 15px}
.welcome h3{font-size:16px;margin-bottom:8px}
.member{left:583px;top:369px;width:156px;height:163px;background:var(--sky);padding:19px 10px;text-align:center}
.member h3{font-size:14px;margin-bottom:9px}
.blog{left:290px;top:496px;width:131px;height:150px;background:var(--orange);padding:17px 10px}
.blog h3{font-size:13px;margin-bottom:14px}
.blog h4{font-family:"Roboto Condensed",sans-serif;font-size:10px;margin-bottom:8px}
.blog .date{font-style:italic;font-size:9px;margin-bottom:8px}
.support{left:426px;top:496px;width:152px;height:150px;background:linear-gradient(160deg,#d8d8d8,#f2f2f2 50%,#9a9a9a)}
.support span{position:absolute;left:0;right:0;bottom:0;height:28px;background:rgba(60,60,60,.7);display:flex;align-items:center;justify-content:center;font-family:"Roboto Condensed",sans-serif;font-size:12px}
.testimonial{left:583px;top:539px;width:156px;height:107px;background:var(--green);padding:8px 12px;text-align:center}
.testimonial .mark{font-family:Georgia,serif;font-weight:700;font-size:44px;line-height:40px;height:28px}
.testimonial cite{display:block;font-style:italic;font-size:8.5px;margin-top:6px}
.go{position:absolute;width:14px;height:14px;border:1.3px solid #fff;border-radius:50%}

/* services */
.services-title{position:absolute;left:0;right:0;top:694px;text-align:center;font-family:"Roboto Condensed",sans-serif;font-size:21px}
.service{position:absolute;top:748px;width:160px;text-align:center}
.service svg{display:block;margin:0 auto}
.service h4{font-family:"Roboto Condensed",sans-serif;font-size:11px;margin-top:14px}
.service p{font-size:7px;line-height:13.6px;color:#333;margin-top:6px}

/* footer */
.site-footer{position:absolute;left:0;top:960px;width:807px;height:240px;background:var(--footer);color:#fff}
.foot-brand{position:absolute;left:60px;top:54px;width:140px;text-align:center}
.foot-brand .sq{width:28px;height:28px;background:#fff;margin:0 auto 12px}
.foot-brand .name{font-family:"Roboto Condensed",sans-serif;font-weight:700;font-size:28px;color:#ddd;letter-spacing:1px}
.foot-brand .tag{font-size:6px;letter-spacing:.3px;color:#ccc}
.foot-col{position:absolute;top:34px}
.foot-col h5{font-family:"Roboto Condensed",sans-serif;font-size:12.5px;margin-bottom:16px}
.foot-col p{font-size:8px;line-height:13.5px}
.contact-line{display:flex;align-items:center;gap:9px;font-size:8px;margin-top:8px}
.social li{list-style:none;display:flex;align-items:center;gap:7px;font-size:10px;margin-bottom:8px}
.social .dot{width:17px;height:17px;border:1.3px solid #ccc;border-radius:50%}
.email-input{width:165px;height:28px;background:#fff;margin-top:12px;color:#555;font-size:7px;display:flex;align-items:center;padding-left:10px}
.subscribe{display:inline-block;margin-top:7px;background:var(--btn-blue);font-family:"Roboto Condensed",sans-serif;font-size:9px;padding:5px 10px}
.foot-bottom{position:absolute;left:0;right:0;top:195px;border-top:1px solid var(--footer-line);text-align:center;font-size:7px;padding-top:18px}
</style>
</head>
<body>

<header class="site-header">
  <div class="brand">
    <div class="brand-mark"></div>
    <div>
      <div class="brand-name">VELOCAB</div>
      <div class="brand-tag">SMOOTH RIDES EVERY SINGLE DAY</div>
    </div>
  </div>
  <div class="header-tools">
    <svg width="15" height="13" viewBox="0 0 15 13"><rect y="0" width="15" height="2.6" fill="#333"/><rect y="5.2" width="15" height="2.6" fill="#333"/><rect y="10.4" width="15" height="2.6" fill="#333"/></svg>
    <svg width="13" height="14" viewBox="0 0 24 24"><path d="M6.6 10.8c1.4 2.8 3.8 5.1 6.6 6.6l2.2-2.2c.3-.3.7-.4 1-.2 1.1.4 2.3.6 3.6.6.6 0 1 .4 1 1V20c0 .6-.4 1-1 1C10.6 21 3 13.4 3 4c0-.6.4-1 1-1h3.5c.6 0 1 .4 1 1 0 1.3.2 2.5.6 3.6.1.3 0 .7-.2 1z" fill="#333"/></svg>
    <svg width="15" height="15" viewBox="0 0 15 15"><circle cx="6" cy="6" r="4.5" fill="none" stroke="#333" stroke-width="2"/><line x1="9.3" y1="9.3" x2="14" y2="14" stroke="#333" stroke-width="2.4"/></svg>
    <div class="login">LOGIN</div>
  </div>
</header>

<section class="hero" role="img" aria-label="Private jet on a runway with business travellers and a limousine">
  <h1 class="hero-title">PRIVATE &amp; BUSINESS</h1>
  <p class="hero-sub">Personalised Transport Service</p>
  <div class="hero-btn">READ MORE</div>
  <div class="slide-arrow" style="left:20px"><svg width="24" height="24"><path d="M14 7l-5 5 5 5" fill="none" stroke="#fff" stroke-width="1.6"/></svg></div>
  <div class="slide-arrow" style="left:758px"><svg width="24" height="24"><path d="M10 7l5 5-5 5" fill="none" stroke="#fff" stroke-width="1.6"/></svg></div>
</section>

<div class="tile quote-box">
  <h3>GET INSTANT QUOTE</h3>
  <div class="field origin"><svg width="9" height="9"><circle cx="4.5" cy="4.5" r="3.6" fill="none" stroke="#333" stroke-width="1.2"/></svg>Origin(Public Location or Exact Address</div>
  <div class="field dest"><svg width="9" height="10" viewBox="0 0 9 10"><path d="M4.5 0a3.3 3.3 0 0 0-3.3 3.3C1.2 5.8 4.5 10 4.5 10s3.3-4.2 3.3-6.7A3.3 3.3 0 0 0 4.5 0z" fill="#333"/><circle cx="4.5" cy="3.3" r="1.2" fill="#fff"/></svg>Destination(Public Location or Exact Address</div>
  <div class="opt" style="margin-top:14px"><svg width="8" height="8"><circle cx="4" cy="4" r="4" fill="#fff"/><path d="M4 2v4M2 4h4" stroke="#706a6a" stroke-width="1.2"/></svg>ADD TRANSPORT</div>
  <div class="opt" style="margin-top:6px"><svg width="8" height="8"><circle cx="4" cy="4" r="3.4" fill="none" stroke="#fff" stroke-width="1.2"/><circle cx="4" cy="4" r="1.5" fill="#fff"/></svg>SHOW OTHER VEHICLES</div>
  <div class="submit">SUBMIT</div>
  <div class="note">*See price guide for extras</div>
</div>

<div class="tile welcome">
  <h3>WELCOME VELOCAB</h3>
  <p>Lorem ipsum dolor sit amet, consectetur adipiscing elit, sed do eiusmod tempor incididunt ut labore et dolore magna aliqua. Ut enim ad minim veniam, quis nostrud exercitation ullamco laboris nisi ut aliquip ex ea commodo consequat. Duis aute irure dolor in reprehenderit in</p>
  <span class="go" style="left:264px;top:100px"></span>
</div>

<div class="tile member">
  <h3>BECOME A MEMBER</h3>
  <p>Sed ut perspiciatis unde omnis iste natus error sit voluptatem santium doloremque laudantium, totam rem aperiam, eaque ipsa quae ab illo inventore veritatis et quasi architecto beatae vitae dicta sunt</p>
  <span class="go" style="left:71px;top:141px"></span>
</div>

<div class="tile blog">
  <h3>BLOG</h3>
  <h4>SED UT PERSPICIATIS</h4>
  <div class="date">22 - JULY</div>
  <p style="line-height:12.8px">Sed ut perspiciatis unde omnis iste natus error sit voluptatem santium doloremque udantium, totam aperiam, eaque</p>
  <span class="go" style="left:106px;top:129px"></span>
</div>

<div class="tile support" role="img" aria-label="Support agent wearing a headset">
  <span>24/7 SUPPORT</span>
</div>

<div class="tile testimonial">
  <div class="mark">“</div>
  <p>Sed ut perspiciatis unde omnis iste natus error sit voluptatem cusantium doloremque laudantium</p>
  <cite>John Doe - Velocab</cite>
</div>

<h2 class="services-title">OUR SERVICES</h2>

<div class="service" style="left:57px">
  <svg width="90" height="90" viewBox="0 0 90 90"><path d="M45 2L88 45 45 88 2 45z" fill="none" stroke="#111" stroke-width="2"/><path d="M28 50v-6l4-7h26l4 7v6z" fill="#777"/><rect x="33" y="39" width="24" height="5" fill="#fff"/><circle cx="34" cy="51" r="3" fill="#777"/><circle cx="56" cy="51" r="3" fill="#777"/></svg>
  <h4>CORPORATE CARS</h4>
  <p>Sed ut perspiciatis unde omnis iste natus error sit voluptatem accusantium dolor-emque laudantium, totam</p>
</div>
<div class="service" style="left:234px">
  <svg width="90" height="90" viewBox="0 0 90 90"><path d="M45 2L88 45 45 88 2 45z" fill="none" stroke="#111" stroke-width="2"/><path d="M33 33h24v14c0 6-6 10-12 12-6-2-12-6-12-12z" fill="#777"/><path d="M45 36v20" stroke="#fff" stroke-width="3"/></svg>
  <h4>DISABILITY TRANSIT</h4>
  <p>Sed ut perspiciatis unde omnis iste natus error sit voluptatem accusantium dolor-emque laudantium, totam</p>
</div>
<div class="service" style="left:412px">
  <svg width="90" height="90" viewBox="0 0 90 90"><path d="M45 2L88 45 45 88 2 45z" fill="none" stroke="#111" stroke-width="2"/><circle cx="45" cy="29" r="4.5" fill="#777"/><path d="M34 36l7 4v20h8V40l7-4-2-3-7 3h-8l-7-3z" fill="#777"/></svg>
  <h4>FAMILY TRANSIT</h4>
  <p>Sed ut perspiciatis unde omnis iste natus error sit voluptatem accusantium dolor-emque laudantium, totam</p>
</div>
<div class="service" style="left:589px">
  <svg width="90" height="90" viewBox="0 0 90 90"><path d="M45 2L88 45 45 88 2 45z" fill="none" stroke="#111" stroke-width="2"/><path d="M19 48v-5l5-5h40l6 5v5z" fill="#777"/><rect x="27" y="40" width="36" height="4" fill="#fff"/><circle cx="26" cy="49" r="3" fill="#777"/><circle cx="63" cy="49" r="3" fill="#777"/></svg>
  <h4>LIMO</h4>
  <p>Sed ut perspiciatis unde omnis iste natus error sit voluptatem accusantium dolor-emque laudantium, totam</p>
</div>

<footer class="site-footer">
  <div class="foot-brand">
    <div class="sq"></div>
    <div class="name">VELOCAB</div>
    <div class="tag">SMOOTH RIDES EVERY SINGLE DAY</div>
  </div>

  <div class="foot-col" style="left:246px">
    <h5>CONTACT US</h5>
    <p>Velocab<br>48 Harbour Lane - Kingsford Street<br>next to the Depot</p>
    <div class="contact-line"><svg width="12" height="12" viewBox="0 0 24 24"><path d="M6.6 10.8c1.4 2.8 3.8 5.1 6.6 6.6l2.2-2.2c.3-.3.7-.4 1-.2 1.1.4 2.3.6 3.6.6.6 0 1 .4 1 1V20c0 .6-.4 1-1 1C10.6 21 3 13.4 3 4c0-.6.4-1 1-1h3.5c.6 0 1 .4 1 1 0 1.3.2 2.5.6 3.6.1.3 0 .7-.2 1z" fill="none" stroke="#ccc" stroke-width="1.6"/></svg>Phone : 555-010-2288</div>
    <div class="contact-line"><svg width="13" height="10" viewBox="0 0 13 10"><rect x=".5" y=".5" width="12" height="9" fill="none" stroke="#ccc"/><path d="M.5 .5l6 5 6-5" fill="none" stroke="#ccc"/></svg>Email : info@velocab.com</div>
  </div>

  <div class="foot-col" style="left:441px;top:36px">
    <h5>SOCIAL MEDIA</h5>
    <ul class="social">
      <li><span class="dot"></span>Linkora</li>
      <li><span class="dot"></span>Chatterly</li>
      <li><span class="dot"></span>Pictora</li>
      <li><span class="dot"></span>clipstream</li>
    </ul>
  </div>

  <div class="foot-col" style="left:575px">
    <h5 style="margin-bottom:12px">SIGN UP FOR NEWSLETTER</h5>
    <p style="font-size:7.2px;line-height:13px;width:170px">Excepteur sint occaecat cupidatat non proident, sunt in culpa qui officia deserunt</p>
    <div class="email-input">Enter email</div>
    <div class="subscribe">SUBSCRIPTION</div>
  </div>

  <div class="foot-bottom">©2017 Velocab. All Rights Reserved.</div>
</footer>

</body>
</html>
```